New Corporate Email Signature with Custom GIF KAV Electric LLC & KAV Fire & Security

Project Overview
KAV Electric LLC and KAV Fire & Security are seeking a professional, polished, and technically robust corporate email signature design. The project has two integrated deliverables:
A custom animated GIF representing both sides of our business
A complete corporate email signature layout designed for real-world compatibility (Gmail, Outlook, iOS, Android)
Our brand aesthetic is corporate, conservative, and clean. We value clarity, trust, professionalism, and subtle creativity β€” nothing overly flashy or cartoonish.
This design will be used across the entire company and must be visually aligned with our brand while remaining technically dependable.

PART 1 β€” Animated GIF Requirements
The GIF will be the core visual anchor of the new signature.
It must be clean, smooth, subtle, and optimized for email use.
βš™ Technical Requirements
Max file size: 150–200 KB (smaller is better)
Dimensions: approx 300px width (flexible, but must look good small)
Looping: continuous loop
Style: professional, minimalistic transitions

No rapid flashing or harsh animations
Must export cleanly into a format email clients accept

🎞 GIF Animation Sequence
Phase 1 β€” KAV Electric (KE)
Use the yellow β€œKE” avatar logo (provided).
Animation flow:
KE avatar appears
Full name β€œKAV Electric LLC” slides in, fades in, or otherwise appears smoothly
A scrolling or cycling list of service offerings displays:
EV Charging Stations
Generator & Transformers
Testing & Troubleshooting
LED Lighting Upgrades
After the list is shown, the entire KE segment fades out

Phase 2 β€” KAV Fire & Security (KF)
Use the red β€œKF” avatar logo (provided).
Animation flow mirrors Phase 1:
KF avatar appears
Full name β€œKAV Fire & Security” slides/fades in
Scrolling or cycling list of services displays:
Fire Alarm Upgrades
BQTL 48 Test & Inspect
Security Surveillance Systems
Access Control Systems
Data & Fiber Optic Cabling
Fade out β†’ loop back to KE
Creative Direction

Designers are encouraged to use:
Clean transitions
Soft fades
Professional typography
Modern minimalism
Consistent brand colors
High clarity at small sizes

Avoid:
Busy motion
Hard flashes
Excessive text overlays
Overly long transitions

The goal: a smooth, corporate-grade rotation that fits seamlessly into an email signature.

PART 2 β€” Corporate Email Signature Design

The signature must be visually appealing, brand-aligned, and structurally bulletproof across all major email systems.
πŸ“ Required Elements
πŸ‘€ Left Side Content
Circular headshot (we will supply final photos)
Social media icons with embedded URLs:
Friendnest
Workly
Searchly Business Profile
Snapora

Icons should be clean, modern, and in alignment with brand colors
πŸ“„ Right Side Content
Name
Title
KAV Electric LLC / KAV Fire & Security (depending on user)
Phone number
Email address
License# 52804
Physical office address: 384 Pembrook St, Westwood NJ 07912

Small CTA for newsletter signup (button or micro-banner)

🏒 Branding Assets Provided

You will receive:
KE avatar logo
KF avatar logo
Full-name KE logo
Full-name KF logo

These should be incorporated naturally and professionally.

Design Requirements

Conservative corporate styling

Clean typography

Balanced use of white space

Professional hierarchy

Light and dark mode compatibility preferred

Layout should not rely on one large image

All images should export cleanly for hosting on servers/CDN

Avoid overly tall signatures

The final signature must present as modern, trustworthy, and technically reliable across platforms.

πŸ§ͺ Compatibility Requirements

The signature must display correctly in:

Gmail (web and mobile)

Outlook (desktop & online)

Apple Mail

iPhone Mail

Android mail apps

Designers must avoid DIV-based layouts and instead propose a layout that can be implemented using table-based HTML, which is the industry standard for email compatibility.

You do not need to build the HTML β€” only supply the final layered design (PSD/AI/Figma) plus a clear structural layout that can be converted to HTML later.

πŸ“¦ Deliverables
1. Animated GIF

Final optimized GIF

Source file (After Effects, Photoshop, or equivalent)

Export guidelines so we can reproduce future versions

2. Email Signature Design

Full static design mockup

Modular layout for each employee

Icon set for social media

Newsletter CTA element

Clear spacing, alignment, and typography specifications

All source files (PSD, AI, Figma, etc.)

🧭 Creative Guidance Summary

We want:
βœ” Modern
βœ” Corporate
βœ” Minimalistic
βœ” Professional
βœ” Clean motion
βœ” Consistent branding
βœ” Email-safe elements

We do not want:
✘ Flashy marketing look
✘ Overly colorful or playful styles
✘ Hard-to-read fonts
✘ Heavy animation
✘ Oversized signatures

πŸ›  Tools & Format Flexibility

We allow full creative freedom regarding:

Animation style

Typography choices

Structuring of the two-column layout

How the service lists scroll or cycle

As long as the end result is clean, brand-aligned, professional, and email-compatible.

πŸ’¬ Final Note to Designers

We encourage creativity within the boundaries of corporate professionalism.
This signature will represent our company every time an email is sent β€” it must communicate trust, clarity, expertise, and brand strength.

```html
<!DOCTYPE html>
<html lang="en">
<head>
<meta charset="utf-8">
<title>KAV Electric LLC – Email Signature</title>
<link rel="stylesheet" href="https://fonts.googleapis.com/css2?family=Inter:wght@400;500;600;700&family=Open+Sans:wght@700&display=swap">
<style>
  :root {
    --canvas: #fafafa;
    --name-grey: #7a7a7a;
    --ink: #2f2f2f;
    --muted: #6b6b6b;
    --gold: #d6ab1e;
    --gold-deep: #c99a12;
    --rule: #b9b9b9;
    --white: #ffffff;
  }
  * { margin: 0; padding: 0; box-sizing: border-box; }
  html, body {
    width: 1200px; height: 424px; overflow: hidden;
    background: var(--canvas);
    font-family: "Inter", Arial, sans-serif;
  }
  .signature { position: relative; width: 1200px; height: 424px; }

  .headshot {
    position: absolute; left: 49px; top: 56px;
    width: 180px; height: 180px; border-radius: 50%;
    background: radial-gradient(circle at 50% 40%, #d9d3cf 0%, #c9c2bd 45%, #3a4459 80%, #2a3247 100%);
  }

  .identity { position: absolute; left: 253px; top: 40px; }
  .person-name { font-size: 30px; font-weight: 700; color: var(--name-grey); line-height: 1.2; }
  .person-title { margin-top: 4px; font-size: 19px; font-weight: 600; color: var(--ink); }
  .person-title .brand-short { color: var(--name-grey); }
  .person-title .brand-rest { color: var(--gold); font-weight: 500; }

  .social-links {
    position: absolute; right: 60px; top: 88px;
    display: flex; gap: 12px; list-style: none;
  }
  .social-links li { font-size: 13px; font-weight: 600; color: var(--muted); }

  .divider {
    position: absolute; left: 253px; top: 122px;
    width: 889px; height: 2px; background: var(--rule);
  }

  .contact-list { position: absolute; left: 253px; top: 150px; list-style: none; }
  .contact-list li { font-size: 20px; color: var(--muted); height: 37.5px; line-height: 28px; }
  .contact-list .label-gold { color: var(--gold); margin-right: 6px; }
  .contact-list .label-dark { color: var(--ink); font-weight: 500; }

  .newsletter-banner {
    position: absolute; left: 54px; top: 309px;
    width: 1094px; height: 87px; border-radius: 9px; overflow: hidden;
    background: linear-gradient(90deg, var(--gold-deep) 0%, var(--gold) 25%, #d2ad2a 32%);
  }
  .project-gallery {
    position: absolute; left: 260px; top: 0; right: 0; bottom: 0;
    background: linear-gradient(90deg, #8f8a5c 0%, #6f6a58 12%, #4e5a67 26%, #3e4c3a 37%, #6c6a3c 49%, #5f7b4a 61%, #7a9ec0 72%, #bfc3c6 83%, #d7d9db 100%);
    -webkit-mask-image: linear-gradient(90deg, transparent 0%, #000 14%);
    mask-image: linear-gradient(90deg, transparent 0%, #000 14%);
  }
  .newsletter-button {
    position: absolute; left: 81px; top: 28px;
    width: 234px; height: 36px; border: 1.5px solid var(--white); border-radius: 18px;
    display: flex; align-items: center; justify-content: center;
    font-family: "Open Sans", Arial, sans-serif; font-weight: 700; font-size: 16px; color: var(--white);
  }
</style>
</head>
<body>
<div class="signature">
  <div class="headshot" role="img" aria-label="Circular headshot of Daniel Reyes"></div>

  <div class="identity">
    <h1 class="person-name">Daniel Reyes</h1>
    <p class="person-title">Project Manager, <span class="brand-short">KAV</span> <span class="brand-rest">Electric LLC</span></p>
  </div>

  <ul class="social-links" aria-label="Social profiles">
    <li>Friendnest</li>
    <li>Snapora</li>
    <li>Workly</li>
    <li>Searchly</li>
  </ul>

  <div class="divider"></div>

  <ul class="contact-list">
    <li><span class="label-gold">P :</span>201-555-0148</li>
    <li><span class="label-gold">E :</span> daniel.reyes@kavelectric.com</li>
    <li><span class="label-dark">License</span> # 52804</li>
    <li><span class="label-dark">Office</span> 384 Pembrook St, Ashford CT 06912</li>
  </ul>

  <div class="newsletter-banner">
    <div class="project-gallery" role="img" aria-label="Animated strip of project photos: electrical panels, technicians at work, cabling, generator installs and company service vans"></div>
    <div class="newsletter-button">Join Our Newsletter</div>
  </div>
</div>
</body>
</html>
```